Larkspur Talent IT Recruiting firm needs a business card design for Recruiters, Sourcers, and Account

We need business cards that allow us to change all contact info, names, titles (Recruiter, Sourcer, Account Manager, Director, CEO, etc) per person since we have three offices, in three cities, Phoenix, Austin, and Las Vegas. We do recruiting and contractors for IT positions (Developers, Architects, Software Engineers, Security Engineers, Help Desk, DBAs, PMs, Scrum Masters, etc.) Our client companies are very diverse from Meridian 100 to silicone Valley type start-ups.

So, while we what hip, techie, and quirky, it still needs to be professional. Primary color we use is blue, with silver as a secondary color.

Target Market(s)

IT, Technology

Industry/Entity Type

Business

Contact Information for Business Card

Company name: Larkspur Talent, Inc.
Website: www.larkspurtalent.example
Logos for Careerloop, Blipster, and Myriada

Name, Title, Office Number, Cell Number, email

Font styles to use
Serif
Sans Serif

Colors
0455a3
d5d5d5

Requirements
Nice to have
• The grey I selected below is not necessary - but, would like silver included. I included a card design (File 3: LTI early trial example.jpg) that I had started on. It's very rough, and not quite what we're looking for, but what we did like is the logo, big, maybe a bit faded, off center, goes out of frame, etc. Still looking for other ideas - you are the pros! But, just an idea of a design element we liked.

```html
<!DOCTYPE html>
<html lang="en">
<head>
<meta charset="utf-8">
<title>Larkspur Talent — Business Card</title>
<link rel="stylesheet" href="https://fonts.googleapis.com/css2?family=Marcellus&family=Roboto+Slab:wght@400;700&display=swap">
<style>
  :root {
    --brand-blue: #0455a3;
    --ink: #1b1b1b;
    --band: #1f1f1f;
    --paper: #ffffff;
    --silver: #d5d5d5;
    --stage: #e9e9e9;
  }
  * { box-sizing: border-box; margin: 0; padding: 0; }
  html, body { width: 1200px; height: 900px; overflow: hidden; }
  body { background: var(--stage); position: relative; font-family: "Roboto Slab", Georgia, serif; color: var(--ink); }

  .card {
    position: absolute; width: 620px; height: 354px;
    background: var(--paper); border-radius: 4px; overflow: hidden;
    box-shadow: 0 8px 24px rgba(0,0,0,.18);
  }
  .card--front { left: 70px; top: 80px; }
  .card--back  { left: 510px; top: 466px; }
  .card svg.band { position: absolute; left: 0; top: 0; }

  .wordmark { position: absolute; font-family: "Marcellus", Georgia, serif; color: var(--ink); line-height: 1; }
  .wordmark__name { display: block; letter-spacing: .06em; }
  .wordmark__unit { display: block; text-align: right; letter-spacing: .18em; color: var(--ink); }
  .wordmark__dot { position: absolute; border-radius: 50%; background: var(--brand-blue); }
  .tagline { position: absolute; font-family: "Marcellus", Georgia, serif; letter-spacing: .22em; color: var(--ink); white-space: nowrap; }

  /* front */
  .card--front .wordmark { left: 110px; top: 100px; }
  .card--front .wordmark__name { font-size: 50px; }
  .card--front .wordmark__unit { font-size: 26px; margin-top: 4px; }
  .card--front .wordmark__dot { width: 22px; height: 22px; left: -34px; top: 16px; }
  .card--front .tagline { left: 0; right: 0; text-align: center; top: 222px; font-size: 17px; }
  .site-url { position: absolute; left: 34px; bottom: 14px; color: #fff; font-size: 11px; letter-spacing: .12em; }

  /* back */
  .card--back .wordmark { left: 62px; top: 60px; }
  .card--back .wordmark__name { font-size: 36px; }
  .card--back .wordmark__unit { font-size: 19px; margin-top: 3px; }
  .card--back .wordmark__dot { width: 16px; height: 16px; left: -26px; top: 11px; }
  .card--back .tagline { left: 62px; top: 142px; font-size: 12.5px; }

  .person { position: absolute; right: 28px; top: 84px; text-align: right; color: #fff; }
  .person__name { font-weight: 700; font-size: 15px; letter-spacing: .04em; }
  .person__title { font-size: 8px; letter-spacing: .08em; margin-top: 2px; }

  .contact-list, .social-list { position: absolute; list-style: none; font-size: 10.5px; letter-spacing: .04em; white-space: nowrap; }
  .contact-list { left: 360px; top: 178px; }
  .contact-list li { display: flex; align-items: center; gap: 12px; height: 17px; text-transform: uppercase; }
  .contact-list svg { width: 10px; height: 10px; fill: var(--brand-blue); flex: none; }

  .social-list { left: 40px; top: 226px; font-weight: 700; }
  .social-list li { display: flex; align-items: center; gap: 14px; height: 22px; text-transform: uppercase; }
  .social-list .marker { width: 9px; height: 9px; border-radius: 50%; background: var(--brand-blue); flex: none; }
</style>
</head>
<body>

  <section class="card card--front" aria-label="Card front">
    <svg class="band" width="620" height="354" viewBox="0 0 620 354" aria-hidden="true">
      <path d="M0 354 V288 H286 C300 288 306 292 316 299 L338 316 H620 V354 Z" fill="var(--band)"/>
    </svg>
    <div class="wordmark">
      <span class="wordmark__dot"></span>
      <span class="wordmark__name">LARKSPUR</span>
      <span class="wordmark__unit">TALENT</span>
    </div>
    <p class="tagline">RISING TO THE CHALLENGE</p>
    <p class="site-url">WWW.LARKSPURTALENT.EXAMPLE</p>
  </section>

  <section class="card card--back" aria-label="Card back">
    <svg class="band" width="620" height="354" viewBox="0 0 620 354" aria-hidden="true">
      <path d="M620 72 V126 H372 C360 126 356 120 358 112 L366 84 C368 76 374 72 384 72 Z" fill="var(--band)"/>
      <path d="M0 354 V296 H348 C362 296 368 300 376 306 L400 326 H620 V354 Z" fill="var(--band)"/>
    </svg>
    <div class="wordmark">
      <span class="wordmark__dot"></span>
      <span class="wordmark__name">LARKSPUR</span>
      <span class="wordmark__unit">TALENT</span>
    </div>
    <p class="tagline">RISING TO THE CHALLENGE</p>

    <div class="person">
      <p class="person__name">DANA R. WHITLOCK</p>
      <p class="person__title">CEO</p>
    </div>

    <ul class="contact-list">
      <li><svg viewBox="0 0 10 10"><path d="M2 0.5 L3.6 2.6 L2.7 3.6 C3.3 5 4.9 6.6 6.4 7.3 L7.4 6.4 L9.5 8 L8.3 9.5 C4.5 9.2 0.8 5.5 0.5 1.7 Z"/></svg>555-014-2271</li>
      <li><svg viewBox="0 0 10 10"><path d="M2.5 0 H7.5 V10 H2.5 Z M3.3 1 V8 H6.7 V1 Z"/></svg>555-014-2271</li>
      <li><svg viewBox="0 0 10 10"><path d="M0 2 H10 V8.5 H0 Z M0.6 2.4 L5 5.8 L9.4 2.4 Z" fill-rule="evenodd"/></svg>dana@larkspurtalent.example</li>
      <li><svg viewBox="0 0 10 10"><circle cx="5" cy="5" r="4.6"/></svg>www.larkspurtalent.example</li>
    </ul>

    <ul class="social-list">
      <li><span class="marker"></span>Myriada.example/Dana R. Whitlock</li>
      <li><span class="marker"></span>Blipster.example/Dana R. Whitlock</li>
      <li><span class="marker"></span>Careerloop.example/Dana R. Whitlock</li>
    </ul>
  </section>

</body>
</html>
```